Animal Eye Clinic needs a Business card

We are a new veterinary ophthalmology practice (Ridgeline Pet Vision Care) and we need a business card designed. We only see animal eyes - we are not a regular veterinary clinic. We already have a logo. We are looking for a professional, good looking business card to hand out to our clients. We are looking for something simple but professional and contemporary. Our logo is likely the only picture/graphic that needs to be on the card.
Updates

Contact Information for Business Card

Delia Vossman, BSc, DVM, MSc, DipACVO
Veterinary Ophthalmologist

Phone: 250.418.3927
Email: ridgelinepetvisioncare@mailbox-example.net
Website: ridgelinepetvisioncare-example.net
Address: 1874 Thornbury Rd
Kelowna, BC, V1X 4M9

Colors

Designer to choose colors to be used in the design.

Requirements
Must have
• Our logo (attached)

```html
<!DOCTYPE html>
<html lang="en">
<head>
<meta charset="utf-8">
<title>Ridgeline Pet Vision Care – Business Card</title>
<link href="https://fonts.googleapis.com/css2?family=Roboto:wght@400;500;700&display=swap" rel="stylesheet">
<style>
  :root {
    --backdrop: #3a3a3a;
    --card: #2b2b2c;
    --card-dark: #262627;
    --teal: #0b9fb3;
    --ink: #f1f1f1;
    --muted: #8a8a8a;
    --faint: #353536;
  }
  * { box-sizing: border-box; margin: 0; padding: 0; }
  html, body {
    width: 1200px; height: 901px; overflow: hidden;
    background: radial-gradient(ellipse at 70% 20%, #4a4a4a 0%, var(--backdrop) 55%, #2a2a2a 100%);
    font-family: "Roboto", Arial, sans-serif;
  }
  .card {
    position: absolute; left: 290px; width: 620px; height: 354px;
    background: var(--card); border-radius: 3px; overflow: hidden;
    box-shadow: 0 10px 30px rgba(0,0,0,.45);
  }
  .card--back { top: 70px; background: var(--card-dark); }
  .card--front { top: 476px; }

  .back-pattern {
    position: absolute; inset: 0;
    background: repeating-linear-gradient(135deg, #2a2a2b 0 40px, #2f2f30 40px 80px);
    opacity: .9;
  }
  .brand {
    display: flex; align-items: center; gap: 10px;
    color: var(--teal); font-weight: 500; text-transform: uppercase;
    font-size: 20px; line-height: 1.15; letter-spacing: .5px;
  }
  .brand__dot { width: 16px; height: 16px; border-radius: 50%; background: var(--teal); flex: none; }
  .card--back .brand { position: absolute; left: 330px; top: 220px; }

  .front-emblem-area {
    position: absolute; right: -60px; top: -10px; width: 380px; height: 380px;
    border-radius: 50%;
    background: radial-gradient(circle at 55% 45%, #3a3a3b 0%, var(--faint) 45%, rgba(43,43,44,0) 72%);
  }
  .card--front .brand { position: absolute; left: 36px; top: 115px; }
  .divider {
    position: absolute; left: 288px; top: 78px; width: 1px; height: 180px; background: #9a9a9a;
  }
  .details { position: absolute; left: 306px; top: 72px; color: var(--ink); }
  .details__name { color: var(--teal); font-weight: 700; font-size: 17px; }
  .details__creds { color: var(--teal); font-size: 11px; font-weight: 400; }
  .details__title { font-size: 16px; margin-top: 2px; }
  .details__address { font-size: 16px; margin-top: 12px; line-height: 1.3; }
  .contacts { list-style: none; margin-top: 12px; font-size: 14px; line-height: 1.5; }
  .contacts li { display: flex; align-items: center; gap: 7px; }
  .contacts svg { width: 12px; height: 12px; fill: var(--teal); flex: none; }
  .contacts .url { color: var(--teal); }
  .stripe { position: absolute; left: 0; right: 0; bottom: 0; height: 10px; background: var(--teal); }
</style>
</head>
<body>
  <section class="card card--back">
    <div class="back-pattern" role="img" aria-label="Repeating faint pattern of the clinic emblem"></div>
    <div class="brand"><span class="brand__dot"></span><span>Ridgeline Pet<br>Vision Care</span></div>
  </section>

  <section class="card card--front">
    <div class="front-emblem-area" role="img" aria-label="Large faint clinic emblem in the background"></div>
    <div class="brand"><span class="brand__dot"></span><span>Ridgeline Pet<br>Vision Care</span></div>
    <div class="divider"></div>
    <div class="details">
      <p><span class="details__name">Delia Vossman</span><span class="details__creds">, BSc, DVM, MSc, DipACVO</span></p>
      <p class="details__title">Veterinary Ophthalmologist</p>
      <p class="details__address">1874 Thornbury Rd<br>Kelowna, BC, V1X 4M9</p>
      <ul class="contacts">
        <li><svg viewBox="0 0 24 24"><path d="M6.6 10.8a15 15 0 0 0 6.6 6.6l2.2-2.2a1 1 0 0 1 1-.25 11 11 0 0 0 3.6.6 1 1 0 0 1 1 1V20a1 1 0 0 1-1 1A17 17 0 0 1 3 4a1 1 0 0 1 1-1h3.5a1 1 0 0 1 1 1c0 1.25.2 2.45.6 3.6a1 1 0 0 1-.25 1z"/></svg>250.418.3927</li>
        <li><svg viewBox="0 0 24 24"><path d="M2 5h20v14H2z M2 5l10 8 10-8" /></svg>ridgelinepetvisioncare@mailbox-example.net</li>
        <li><svg viewBox="0 0 24 24"><circle cx="12" cy="12" r="10"/></svg><span>www.<span class="url">ridgelinepetvisioncare-example</span>.net</span></li>
      </ul>
    </div>
    <div class="stripe"></div>
  </section>
</body>
</html>
```